NZ First of it's kind solutions directory and marketplace for busy Mums needs a business card design

We need a business card design for our new nationwide business in NZ (long term plans to go global). We provide solutions to the everyday challenges that busy Mums face by connecting them with quality communities and suppliers of carefully selected, relevant products and services. We sell direct via our online marketplace. The final design should communicate our values of inclusivity, quality and smart solutions. Colours should incorporate our logo colour palette of #477077 and #6ba8b2. Our website is at https://www.brightnestmums.example

Target Market(s)

busy Mums, Age 28 – 50, female, income over $100K, location main centres NZ primarily but NZ wide. Is likely juggling work or career with a young family. Probably had hobbies which have fallen by the wayside.
-Wants to succeed in her chosen career without compromising on family life
-to successfully juggle her career without feeling like she is compromising her children
- Is time poor, something always has to give and it’s generally her health (she’ll stay up late, get stressed)
- probably ex corporate or professional career. Has discretional income

Industry/Entity Type

Business

Contact Information for Business Card

Lena Forbisher, Founder, BrightNestMums.example (Strapline Tap; Gather; Sorted), 47 Kowhai Terrace, Ellerslie, Auckland 1051, New Zealand. Mob: 021 483 517 Ph: +64 (0)9 571 4860

Font styles to use
Other font styles liked:
• Raleway, and/or Architects Daughter

Colors
00a990
33b8a4
86cfc6
cfeae6

Requirements
Must have
• the above details, streamline. the logo and colours associated with those logos
Should not have
• foil or metallic colours

```html
<!DOCTYPE html>
<html lang="en">
<head>
<meta charset="utf-8">
<title>BrightNestMums Business Card</title>
<link href="https://fonts.googleapis.com/css2?family=Work+Sans:wght@400;500;600&display=swap" rel="stylesheet">
<style>
  :root {
    --backdrop: #2a2a2c;
    --card: #1c1c1e;
    --card-edge: #262628;
    --accent-band: #3db4d4;
    --brand-teal: #5b9aa4;
    --name-teal: #6ba8b2;
    --text-light: #f2f2f2;
    --divider: #e8e8e8;
  }
  * { margin: 0; padding: 0; box-sizing: border-box; }
  html, body {
    width: 1200px;
    height: 900px;
    overflow: hidden;
    background: var(--backdrop);
    font-family: "Work Sans", Arial, sans-serif;
  }
  .canvas {
    position: relative;
    width: 1200px;
    height: 900px;
  }
  .card {
    position: absolute;
    left: 265px;
    width: 670px;
    height: 383px;
    background: linear-gradient(135deg, var(--card) 0%, var(--card) 55%, var(--card-edge) 100%);
    box-shadow: 0 14px 30px rgba(0,0,0,0.45);
    overflow: hidden;
  }
  .card::after {
    content: "";
    position: absolute;
    left: 0; right: 0; bottom: 0;
    height: 8px;
    background: var(--accent-band);
  }
  .card-front { top: 40px; }
  .card-back { top: 470px; }

  .brand {
    display: flex;
    align-items: center;
    gap: 14px;
  }
  .brand-dot {
    width: 38px;
    height: 38px;
    border-radius: 50%;
    background: var(--brand-teal);
    flex: none;
  }
  .brand-name {
    color: var(--brand-teal);
    font-weight: 600;
    letter-spacing: -0.5px;
    white-space: nowrap;
  }
  .card-front .brand {
    position: absolute;
    left: 0; right: 0; top: 0; bottom: 8px;
    justify-content: center;
  }
  .card-front .brand-name { font-size: 44px; }

  .card-back .brand {
    position: absolute;
    left: 38px;
    top: 150px;
    gap: 10px;
  }
  .card-back .brand-dot { width: 26px; height: 26px; }
  .card-back .brand-name { font-size: 28px; }

  .divider {
    position: absolute;
    left: 340px;
    top: 110px;
    width: 2px;
    height: 170px;
    background: var(--divider);
  }
  .contact {
    position: absolute;
    left: 364px;
    top: 108px;
    color: var(--text-light);
  }
  .contact-name {
    color: var(--name-teal);
    font-size: 30px;
    font-weight: 500;
    line-height: 1.05;
    white-space: nowrap;
  }
  .contact-role {
    font-size: 16px;
    letter-spacing: 0.5px;
    margin-bottom: 12px;
  }
  .contact-address {
    font-size: 16px;
    letter-spacing: 0.6px;
    line-height: 1.3;
    font-style: normal;
    margin-bottom: 6px;
    white-space: nowrap;
  }
  .contact-line {
    display: flex;
    align-items: center;
    gap: 8px;
    font-size: 16px;
    letter-spacing: 0.6px;
    line-height: 1.35;
    white-space: nowrap;
  }
  .contact-icon {
    width: 11px;
    height: 11px;
    flex: none;
  }
</style>
</head>
<body>
<main class="canvas">
  <section class="card card-front" aria-label="Card front">
    <div class="brand">
      <span class="brand-dot"></span>
      <span class="brand-name">BrightNestMums</span>
    </div>
  </section>

  <section class="card card-back" aria-label="Card back">
    <div class="brand">
      <span class="brand-dot"></span>
      <span class="brand-name">BrightNestMums</span>
    </div>
    <div class="divider"></div>
    <div class="contact">
      <div class="contact-name">Lena Forbisher</div>
      <div class="contact-role">Founder</div>
      <address class="contact-address">47 Kowhai Terrace, Ellerslie<br>Auckland 1051, New Zealand</address>
      <div class="contact-line">
        <svg class="contact-icon" viewBox="0 0 12 12" aria-hidden="true"><rect x="3" y="0.5" width="6" height="11" rx="1" fill="none" stroke="#6ba8b2" stroke-width="1.2"/><circle cx="6" cy="9.5" r="0.7" fill="#6ba8b2"/></svg>
        <span>021 483 517</span>
      </div>
      <div class="contact-line">
        <svg class="contact-icon" viewBox="0 0 12 12" aria-hidden="true"><path d="M2.5 1 L4.5 1 L5.2 3.6 L4 4.6 Q5 7 7.4 8 L8.4 6.8 L11 7.5 L11 9.5 Q10.5 11 9 11 Q3.5 10.5 1 3 Q1 1.5 2.5 1 Z" fill="#6ba8b2"/></svg>
        <span>+64 (0)9 571 4860</span>
      </div>
      <div class="contact-line">
        <svg class="contact-icon" viewBox="0 0 12 12" aria-hidden="true"><circle cx="6" cy="6" r="5" fill="none" stroke="#6ba8b2" stroke-width="1"/><ellipse cx="6" cy="6" rx="2.2" ry="5" fill="none" stroke="#6ba8b2" stroke-width="0.9"/><line x1="1" y1="6" x2="11" y2="6" stroke="#6ba8b2" stroke-width="0.9"/></svg>
        <span>www.brightnestmums.example</span>
      </div>
    </div>
  </section>
</main>
</body>
</html>
```